Business Card Design Project for Heron Lending

Hello there,

We are looking for a business card design for our new Heron Lending car financing company. We are looking for a business card that will include:

- An address
- Telephone number and extension
- Employee Name
- Employee Title
- Our logo and name clearly visible

We are including our logo with this writeup, we are looking to convey friendliness, trus and memorability. Colors and everything else is up to you.

Target Market(s)

18-34 year old males and females

Industry/Entity Type

Business

```html
<!DOCTYPE html>
<html lang="en">
<head>
<meta charset="utf-8">
<title>Heron Lending — Business Card</title>
<link href="https://fonts.googleapis.com/css2?family=Open+Sans:wght@400;600;700&display=swap" rel="stylesheet">
<style>
  :root {
    --backdrop: #e9e9e9;
    --card: #ffffff;
    --card-back: #f4f4f2;
    --brand-blue: #2d5384;
    --ink: #2b2a28;
    --art-dark: #33302d;
    --art-light: #efefed;
  }
  * { box-sizing: border-box; margin: 0; padding: 0; }
  html, body {
    width: 1200px;
    height: 675px;
    overflow: hidden;
    background: var(--backdrop);
    font-family: "Open Sans", Arial, sans-serif;
  }
  .sheet {
    width: 1200px;
    height: 675px;
    display: flex;
    align-items: center;
    justify-content: center;
    gap: 40px;
  }
  .card {
    position: relative;
    width: 520px;
    height: 297px;
    overflow: hidden;
    box-shadow: 0 2px 10px rgba(0,0,0,0.12);
  }

  /* Front */
  .card--front { background: var(--card); }
  .front__band {
    position: absolute;
    left: 0;
    top: 186px;
    width: 345px;
    height: 36px;
    background: var(--brand-blue);
  }
  .brand {
    position: absolute;
    left: 345px;
    top: 118px;
    width: 150px;
    display: flex;
    flex-direction: column;
    align-items: center;
  }
  .brand__rule {
    width: 150px;
    height: 2px;
    background: var(--ink);
    margin-bottom: 8px;
  }
  .brand__name {
    color: var(--brand-blue);
    font-weight: 600;
    font-size: 26px;
    letter-spacing: 5px;
    line-height: 1;
  }
  .brand__sub {
    color: var(--brand-blue);
    font-weight: 600;
    font-size: 10px;
    letter-spacing: 7px;
    margin-top: 4px;
  }
  .brand__mark {
    position: absolute;
    left: 478px;
    top: 92px;
    width: 24px;
    height: 24px;
    background: var(--brand-blue);
  }

  /* Back */
  .card--back { background: var(--card-back); }
  .back__art {
    position: absolute;
    right: 0;
    top: 0;
    width: 330px;
    height: 220px;
    background: linear-gradient(120deg, var(--art-light) 0%, var(--art-dark) 45%, var(--art-dark) 80%, var(--art-light) 100%);
  }
  .person {
    position: absolute;
    left: 24px;
    top: 112px;
  }
  .person__name {
    color: var(--brand-blue);
    font-weight: 700;
    font-size: 15px;
  }
  .person__title {
    color: var(--ink);
    font-size: 10px;
    margin-top: 2px;
  }
  .contact {
    position: absolute;
    left: 24px;
    bottom: 28px;
    list-style: none;
    color: var(--ink);
    font-size: 12px;
  }
  .contact__item {
    display: flex;
    align-items: center;
    gap: 6px;
    margin-top: 4px;
  }
  .contact__icon { width: 11px; height: 11px; fill: var(--brand-blue); }
</style>
</head>
<body>
<main class="sheet">
  <section class="card card--front" aria-label="Card front">
    <div class="front__band"></div>
    <div class="brand__mark"></div>
    <div class="brand">
      <div class="brand__rule"></div>
      <span class="brand__name">HERON</span>
      <span class="brand__sub">LENDING</span>
    </div>
  </section>

  <section class="card card--back" aria-label="Card back">
    <div class="back__art" role="img" aria-label="Large black and white illustration of the brand animal walking, cropped at the card edge"></div>
    <div class="person">
      <p class="person__name">Your Long Name</p>
      <p class="person__title">Your Title</p>
    </div>
    <ul class="contact">
      <li class="contact__item">
        <svg class="contact__icon" viewBox="0 0 24 24" aria-hidden="true"><path d="M6.6 10.8a15.1 15.1 0 0 0 6.6 6.6l2.2-2.2c.3-.3.7-.4 1-.2 1.1.4 2.3.6 3.6.6.6 0 1 .4 1 1V20c0 .6-.4 1-1 1A17 17 0 0 1 3 4c0-.6.4-1 1-1h3.5c.6 0 1 .4 1 1 0 1.3.2 2.5.6 3.6.1.3 0 .7-.2 1z"/></svg>
        <span>00.00.00.0000</span>
      </li>
      <li class="contact__item">
        <svg class="contact__icon" viewBox="0 0 24 24" aria-hidden="true"><path d="M12 2a7 7 0 0 0-7 7c0 5.2 7 13 7 13s7-7.8 7-13a7 7 0 0 0-7-7zm0 9.5A2.5 2.5 0 1 1 12 6.5a2.5 2.5 0 0 1 0 5z"/></svg>
        <span>Your Commercial or office address</span>
      </li>
    </ul>
  </section>
</main>
</body>
</html>
```